Website for Excavator and Earthworks Company

We require a modern, sleek and practical website for our newly created earthworks/excavator business in Perth, Western Australia called Bluegum Ridge Earthworks.

The website should have a modern, cutting edge feel but only needs to be relatively simplistic in it's layout and eventual functionality.

Some pages it should have would be Home, About, Projects and Contact Us.

```html
<!DOCTYPE html>
<html lang="en">
<head>
<meta charset="utf-8">
<title>Bluegum Ridge Earthworks</title>
<link rel="stylesheet" href="https://fonts.googleapis.com/css2?family=Poppins:wght@400;500;600;700;800&display=swap">
<style>
:root{
  --lime:#d2e600;
  --lime-btn:#b5f000;
  --navy-btn:#0b1fa3;
  --ink:#111;
  --muted:#444;
  --mint:#f2fde6;
  --deep:#0b3a52;
  --white:#fff;
}
*{box-sizing:border-box;margin:0;padding:0}
html,body{width:1200px;height:2792px;overflow:hidden}
body{position:relative;font-family:"Poppins",sans-serif;color:var(--ink);background:var(--white)}

/* hero */
.hero{position:absolute;left:0;top:0;width:1200px;height:672px;overflow:hidden}
.hero-photo{position:absolute;inset:0;background:
  radial-gradient(ellipse at 70% 40%,rgba(200,100,40,.55),transparent 55%),
  linear-gradient(180deg,#2d4e74 0%,#4a6a86 30%,#5a4a3c 70%,#3a2e26 100%)}
.hero-shade{position:absolute;inset:0;background:rgba(10,25,45,.35)}
.hero-wave{position:absolute;left:0;top:480px}
.brand{position:absolute;display:flex;align-items:center;gap:10px;color:var(--white);font-weight:700;font-size:20px;letter-spacing:1px;white-space:nowrap}
.brand-mark{width:26px;height:26px;background:var(--lime)}
.pill{position:absolute;top:22px;height:33px;border-radius:17px;display:flex;align-items:center;gap:7px;padding:0 14px;font-size:15px;font-weight:500;white-space:nowrap}
.pill-mail{left:763px;width:202px;border:2px solid var(--white);color:var(--white)}
.pill-phone{left:980px;width:150px;background:var(--lime);color:var(--ink)}
.nav{position:absolute;top:73px;left:430px;display:flex;gap:42px;color:var(--white);font-size:17px;font-weight:500}
.hero-title{position:absolute;left:300px;top:183px;font-size:52px;line-height:1;font-weight:700;color:var(--white);letter-spacing:-.5px;white-space:nowrap}
.hero-title span{color:var(--lime);font-weight:500}
.hero-text{position:absolute;left:300px;top:247px;width:545px;font-size:15px;line-height:22px;color:var(--white);font-weight:500}
.btn{position:absolute;display:flex;align-items:center;justify-content:center;font-size:17px;font-weight:500}
.btn-see{left:300px;top:334px;width:145px;height:45px;background:var(--navy-btn);color:var(--white)}
.btn-contact{left:460px;top:334px;width:157px;height:45px;border:2px solid var(--white);color:var(--white)}

/* about */
.section-title{position:absolute;width:1200px;text-align:center;font-weight:700;font-size:42px;line-height:1.2}
.photo{position:absolute;border-radius:3px}
.about-copy{position:absolute;left:621px;top:836px;width:512px}
.about-copy h3{font-size:20px;font-weight:700;margin-bottom:6px}
.about-copy p{font-size:15px;line-height:29px;color:#222}
.about-copy a{display:inline-block;margin-top:18px;font-weight:700;font-size:17px;color:var(--ink);text-decoration:underline}

/* projects */
.projects{position:absolute;left:0;top:1176px;width:1200px;height:656px;background:var(--mint)}
.projects-title{top:56px;color:#2a2a2a}
.projects-title span{color:var(--lime)}
.projects-sub{position:absolute;top:124px;width:1200px;text-align:center;font-size:15px;line-height:22px;color:#333}
.card{position:absolute;top:201px;width:297px;height:406px;background:var(--white);border-radius:4px;box-shadow:0 2px 8px rgba(0,0,0,.12);padding:4px}
.card-photo{height:190px}
.card h4{margin:14px 16px 0;font-size:20px;line-height:22px;font-weight:700;color:#222}
.card p{margin:12px 16px 0;font-size:12.5px;line-height:18.5px;color:#444}
.card-btn{display:inline-flex;align-items:center;gap:6px;margin:12px 16px 0;height:36px;padding:0 20px;background:var(--lime-btn);font-weight:700;font-size:14px}

/* contact */
.contact{position:absolute;left:0;top:1832px;width:1200px;height:705px;overflow:hidden}
.contact-photo{position:absolute;inset:0;background:
  radial-gradient(ellipse at 75% 45%,#3b6478 0%,transparent 50%),
  linear-gradient(100deg,#10303f 0%,#1d4659 60%,#1a3b4c 100%)}
.contact-panel{position:absolute;left:60px;top:35px;width:599px;height:670px;background:rgba(12,40,56,.82);border-radius:8px 8px 0 0}
.contact-panel h2{position:absolute;left:42px;top:36px;font-size:44px;line-height:1.2;font-weight:700;color:var(--white)}
.field{position:absolute;left:42px;width:516px}
.field label{display:block;color:var(--white);font-size:15px;line-height:20px;font-weight:500;margin-bottom:4px}
.field .input{height:40px;border:1.5px solid #ccd;border-radius:3px;color:#aab;font-size:14px;padding:8px 0 0 1px}
.field .area{height:87px;padding-top:2px}
.submit{position:absolute;left:42px;top:583px;width:144px;height:46px;background:var(--lime);display:flex;align-items:center;justify-content:center;font-weight:700;font-size:17px}

/* footer */
.footer{position:absolute;left:0;top:2537px;width:1200px;height:233px;background:var(--deep);color:var(--white)}
.footer h5{position:absolute;top:52px;font-size:21px;font-weight:500}
.footer ul{position:absolute;top:98px;list-style:none;font-size:17px;line-height:30px}
.newsletter{position:absolute;left:864px;top:96px;display:flex;align-items:center;gap:6px}
.newsletter .email{width:172px;height:23px;background:var(--white);color:#888;font-size:13px;padding:2px 3px}
.newsletter .go{width:24px;height:24px;background:var(--white);display:flex;align-items:center;justify-content:center}
.socials{position:absolute;left:864px;top:156px;display:flex;gap:17px}
.socials span{width:35px;height:27px;border:1.5px solid #cdd;border-radius:3px}
.copyright{position:absolute;left:0;top:2770px;width:1200px;height:22px;background:var(--lime);text-align:center;font-size:10px;line-height:22px;color:#222}
</style>
</head>
<body>

<header class="hero">
  <div class="hero-photo" role="img" aria-label="Orange excavator on a city construction site under a blue sky"></div>
  <div class="hero-shade"></div>
  <svg class="hero-wave" width="1200" height="192" viewBox="0 0 1200 192">
    <path d="M0 100 C150 40 300 50 450 85 C600 110 750 100 900 75 C1050 50 1150 20 1200 15 L1200 192 L0 192Z" fill="#e9f5a8" opacity=".7"/>
    <path d="M0 112 C160 58 300 70 460 100 C600 122 760 108 900 88 C1040 68 1150 40 1200 32 L1200 192 L0 192Z" fill="#d2e600"/>
    <path d="M0 142 C160 76 310 82 470 110 C610 130 760 118 900 102 C1040 86 1150 58 1200 50 L1200 192 L0 192Z" fill="#ffffff"/>
  </svg>
  <div class="brand" style="left:65px;top:46px"><span class="brand-mark"></span>BLUEGUM RIDGE</div>
  <div class="pill pill-mail">
    <svg width="15" height="12" viewBox="0 0 15 12"><rect x="1" y="1" width="13" height="10" fill="none" stroke="#fff" stroke-width="1.6"/><path d="M1 1 L7.5 7 L14 1" fill="none" stroke="#fff" stroke-width="1.6"/></svg>
    info@bluegum.com.au
  </div>
  <div class="pill pill-phone">
    <svg width="14" height="14" viewBox="0 0 24 24"><path d="M6.6 10.8a15 15 0 006.6 6.6l2.2-2.2a1 1 0 011-.25 11.4 11.4 0 003.6.6 1 1 0 011 1V20a1 1 0 01-1 1A17 17 0 013 4a1 1 0 011-1h3.5a1 1 0 011 1 11.4 11.4 0 00.6 3.6 1 1 0 01-.25 1z" fill="#111"/></svg>
    08 5550 1234
  </div>
  <nav class="nav"><span>Home</span><span>About</span><span>Projects</span><span>Contact Us</span></nav>
  <h1 class="hero-title">SOLUTIONS <span>for your need</span></h1>
  <p class="hero-text">Lorem ipsum dolor sit, amet consectetur adipisicing elit. Fugiat delectus in consequuntur, facilis aliquid porro voluptatum consectetur consequatur doloremque quod?</p>
  <div class="btn btn-see">See more</div>
  <div class="btn btn-contact">Contact Us</div>
</header>

<section>
  <h2 class="section-title" style="top:662px">About Us</h2>
  <div class="photo" style="left:60px;top:777px;width:227px;height:177px;background:linear-gradient(180deg,#4f8fd6,#c77a3c 70%,#6a5a48)" role="img" aria-label="Orange excavator beside apartment towers"></div>
  <div class="photo" style="left:60px;top:963px;width:227px;height:178px;background:linear-gradient(160deg,#3e6a3a,#d9c420 55%,#385a2c)" role="img" aria-label="Yellow excavator clearing a green field"></div>
  <div class="photo" style="left:298px;top:777px;width:282px;height:364px;background:linear-gradient(180deg,#c9d6e3 0%,#d6a868 55%,#8a5a34 100%)" role="img" aria-label="Yellow backhoe digging in dusty earth"></div>
  <div class="about-copy">
    <h3>History</h3>
    <p>Lorem ipsum dolor sit amet, consectetur adipisicing elit. Sed, perferendis? Quod deleniti alias laborum dolores, numquam, omnis at ullam unde nemo officia temporibus quia quis libero neque ducimus recusandae. Minus repudiandae molestiae consectetur, aut illo voluptatibus fugiat? Ea placeat iure dicta et provident, porro nulla, sit eveniet ratione, dolores laudantium.</p>
    <a>Company Founder</a>
  </div>
</section>

<section class="projects">
  <h2 class="section-title projects-title">Our <span>projects</span></h2>
  <p class="projects-sub">Lorem ipsum dolor, sit amet consectetur adipisicing elit.<br>Excepturi, consequuntur.</p>
  <article class="card" style="left:144px">
    <div class="card-photo" style="background:linear-gradient(180deg,#8a9aa2,#d39a2a 55%,#555)" role="img" aria-label="Excavator on a rocky riverbed"></div>
    <h4>Irrigation dredging</h4>
    <p>Lorem ipsum dolor sit amet consectetur adipisicing elit. Distinctio ad qui officia velit obcaecati quod aliquid, voluptatibus similique recusandae dolorem ab harum impedit incidunt</p>
    <span class="card-btn">Contact Us <svg width="14" height="12" viewBox="0 0 14 12"><path d="M1 6h11M7 1l5 5-5 5" fill="none" stroke="#111" stroke-width="2"/></svg></span>
  </article>
  <article class="card" style="left:452px">
    <div class="card-photo" style="background:linear-gradient(180deg,#a4aaa2,#c86a2a 60%,#4a3a2c)" role="img" aria-label="Excavator levelling soil on a slope"></div>
    <h4>Land leveling of agricultural land</h4>
    <p>The process of dredging the layer of soil or unwanted material above the rock deposit is removed first, for the land for the factory building.</p>
    <span class="card-btn">Contact Us <svg width="14" height="12" viewBox="0 0 14 12"><path d="M1 6h11M7 1l5 5-5 5" fill="none" stroke="#111" stroke-width="2"/></svg></span>
  </article>
  <article class="card" style="left:760px">
    <div class="card-photo" style="background:linear-gradient(180deg,#9fb6c8,#c9922c 55%,#7a5038)" role="img" aria-label="Excavator digging an irrigation trench"></div>
    <h4>Excavation of land for irrigation</h4>
    <p>Excavation work for irrigation is a crucial part of the construction and rehabilitation of water networks to ensure smooth distribution flow.</p>
    <span class="card-btn">Contact Us <svg width="14" height="12" viewBox="0 0 14 12"><path d="M1 6h11M7 1l5 5-5 5" fill="none" stroke="#111" stroke-width="2"/></svg></span>
  </article>
</section>

<section class="contact">
  <div class="contact-photo" role="img" aria-label="Blurred office meeting in blue tones"></div>
  <div class="contact-panel">
    <h2>Contact Us</h2>
    <div class="field" style="top:127px"><label>First Name</label><div class="input">Your name..</div></div>
    <div class="field" style="top:208px"><label>Last Name</label><div class="input">Your last name..</div></div>
    <div class="field" style="top:289px"><label>e-mail</label><div class="input">Your e-mail..</div></div>
    <div class="field" style="top:370px"><label>Mobile</label><div class="input">Your mobile..</div></div>
    <div class="field" style="top:453px"><label>Subject</label><div class="input area">Write something..</div></div>
    <div class="submit">Submit</div>
  </div>
</section>

<footer class="footer">
  <div class="brand" style="left:125px;top:96px"><span class="brand-mark"></span>BLUEGUM RIDGE</div>
  <h5 style="left:357px">Quick Links</h5>
  <ul style="left:357px"><li>Home</li><li>About Us</li><li>Projects</li><li>Contact Us</li></ul>
  <h5 style="left:610px">Projects</h5>
  <ul style="left:610px"><li>Instalation Irrigation</li><li>Land leveling</li><li>Excavation of land</li></ul>
  <h5 style="left:864px">Newsletter</h5>
  <div class="newsletter">
    <svg width="17" height="13" viewBox="0 0 15 12"><rect x="1" y="1" width="13" height="10" fill="none" stroke="#fff" stroke-width="1.4"/><path d="M1 1 L7.5 7 L14 1" fill="none" stroke="#fff" stroke-width="1.4"/></svg>
    <div class="email">Enter your email</div>
    <div class="go"><svg width="14" height="12" viewBox="0 0 14 12"><path d="M1 6h11M7 1l5 5-5 5" fill="none" stroke="#111" stroke-width="2"/></svg></div>
  </div>
  <div class="socials"><span></span><span></span><span></span><span></span></div>
</footer>
<div class="copyright">Copyright © 2025 BLUEGUM RIDGE Earth Works - All Rights Reserved.</div>

</body>
</html>
```